Pastor's Lantern: How To Help Church Leaders Remain Strong In Their Callings.

I have created a 250-page book tentatively entitled, Pastor's Lantern, subtitle: A Handbook To Help Church Leaders Remain Strong in Their Callings. The chapters are taken from my podcast of the same name on TuneVault and website: pastorslantern-example.com which will need updating soon. The purpose of the book is to provide practical solutions to pastors/leaders about everyday issues faced in ministry such as loneliness, financial challenges, a pastor's family problems, sexual temptation ...etc. You can get an idea of the topics from TuneVault.
Updates

As mentioned in the brief, I am looking for something that will communicate solutions. My podcast, Pastor's Lantern from which this material originates is all about practical help for local pastors in facing the challenges of daily ministry. The logo I sent was designed for concept purposes only. It does not need to be on the cover necessarily unless it feeds into the overall theme.

Target Market(s)

Pastors and Church Leaders in the Christian Faith

Industry/Entity Type

Religious

Font styles to use
Serif

Colors

Designer to choose colors to be used in the design.

Requirements
Must have
• Crisp copy and lines. People see covers for 3 seconds. If they are not drawn in by complicated themes, I have failed. Many of the designs so far do not address the topic of the book in a way that impacts. This is about a toolbox or book that provides solutions to their everyday challenges. If it doesn't somehow point to tools, it should instead point to getting solutions.
Nice to have
• I have included a copy of my current logo. If you can incorporate it, fine. If you have a better idea, I am open to that and would be interested in contributing more if the logo is superior. The logo is not essential to either front or back cover..
Should not have
• Simplistic religious themes from often used pics. I will peruse other book covers in my genre. If I find the same pic used, it disqualifies the design immediately no matter how much I like it. Target audience is ministers. Simplistic cross designs have gotten less votes so far in polling. I want to grab attention with a compelling picture that communicates solutions.

```html
<!DOCTYPE html>
<html lang="en">
<head>
<meta charset="UTF-8">
<title>Pastor's Lantern — Book Cover</title>
<link rel="stylesheet" href="https://fonts.googleapis.com/css2?family=Cinzel:wght@400;500&display=swap">
<style>
  :root {
    --sky-top: #f3f3f2;
    --sky-mid: #eceeef;
    --sky-low: #dbe1e6;
    --sky-bottom: #c9d3dc;
    --iron-deep: #2e211b;
    --iron: #4a362b;
    --iron-light: #6e5646;
    --rope: #a89a83;
    --rope-light: #c4b8a3;
    --ink: #111111;
    --ink-soft: #2a2a2a;
  }
  html, body {
    margin: 0;
    padding: 0;
    width: 735px;
    height: 1200px;
    overflow: hidden;
    background: var(--sky-top);
  }
  .cover {
    position: relative;
    width: 735px;
    height: 1200px;
    overflow: hidden;
    font-family: "Cinzel", serif;
    color: var(--ink);
    background: linear-gradient(180deg, var(--sky-top) 0%, var(--sky-mid) 60%, var(--sky-low) 82%, var(--sky-bottom) 100%);
  }
  .cover-photo {
    position: absolute;
    top: 62px;
    left: 0;
    width: 735px;
    height: 720px;
    background: linear-gradient(118deg,
      var(--iron-deep) 0%,
      var(--iron) 26%,
      var(--iron-light) 40%,
      var(--rope) 56%,
      var(--rope-light) 68%,
      rgba(236, 238, 239, 0) 86%);
    -webkit-mask-image: linear-gradient(180deg, #000 0%, #000 70%, transparent 100%);
    mask-image: linear-gradient(180deg, #000 0%, #000 70%, transparent 100%);
  }
  .author {
    position: absolute;
    top: 12px;
    left: 0;
    width: 100%;
    margin: 0;
    text-align: center;
    font-size: 37px;
    font-weight: 400;
    letter-spacing: 0.15em;
    margin-left: 0.075em;
  }
  .title {
    position: absolute;
    top: 870px;
    left: 0;
    width: 100%;
    margin: 0;
    text-align: center;
    font-weight: 400;
  }
  .title-lead {
    display: block;
    font-size: 58px;
    letter-spacing: 0.34em;
    margin-right: -0.34em;
    line-height: 1.1;
  }
  .title-main {
    display: block;
    font-size: 112px;
    letter-spacing: 0.02em;
    line-height: 1.05;
    margin-top: 0;
  }
  .subtitle {
    position: absolute;
    top: 1070px;
    left: 0;
    width: 100%;
    margin: 0;
    text-align: center;
    font-size: 22px;
    line-height: 28px;
    letter-spacing: 0.02em;
    color: var(--ink-soft);
  }
</style>
</head>
<body>
  <main class="cover">
    <div class="cover-photo" role="img" aria-label="Photograph of a heavy rusted iron hook gripping a taut braided rope against a pale overcast sky"></div>
    <p class="author">CORWIN M. HALDANE</p>
    <h1 class="title">
      <span class="title-lead">PASTOR'S</span>
      <span class="title-main">LANTERN</span>
    </h1>
    <p class="subtitle">A HANDBOOK TO HELP CHURCH LEADERS<br>REMAIN STRONG IN THEIR CALLINGS</p>
  </main>
</body>
</html>
```